Business Card for Vorla Parts Wholesale supplier

Hi There! I need a new business card for our company. We are specialized in selling Vorla parts, mostly we sell new LCD screens for Zelnar and Drelks. I would like to see that back in the design.

You can find the colors and logo's on our website: www.hartuvo.nl

Industry/Entity Type

Business

Contact Information for Business Card

My Details:
Tobias Lindqvist

Phone: 0031687203316
E-mail: Tobias@hartuvo.nl

Slogan: "Because Quality Matters"

Font styles to use
Sans Serif

Colors

Designer to choose colors to be used in the design.

Requirements
Must have
• A Black backside with the Hartuvo logo on it. The front side should be clean with only my contact details.
• But I'm also open for something really different or awesome!
Nice to have
• Remember that we are in the parts & repairing industry, So i'll be handing those business cards mainly to repair companies. Maybe you can do something with that thought :)

```html
<!DOCTYPE html>
<html lang="en">
<head>
<meta charset="utf-8">
<title>Hartuvo – Business Card</title>
<link rel="stylesheet" href="https://fonts.googleapis.com/css2?family=Exo+2:wght@600&family=Open+Sans:wght@400;600&display=swap">
<style>
  :root {
    --page: #e8e5e1;
    --card-white: #ffffff;
    --card-black: #0c0a09;
    --pattern-tone: #1d1612;
    --orange: #f07524;
    --ink: #111111;
    --grey: #555555;
    --white: #ffffff;
  }
  * { margin: 0; padding: 0; box-sizing: border-box; }
  html, body {
    width: 1200px;
    height: 987px;
    overflow: hidden;
    background: var(--page);
  }
  .card {
    position: absolute;
    left: 293px;
    width: 615px;
    height: 350px;
    overflow: hidden;
    box-shadow: 0 2px 8px rgba(0,0,0,0.18);
  }
  .card--front { top: 131px; background: var(--card-white); }
  .card--back { top: 506px; background: var(--card-black); }

  .accent-panel {
    position: absolute;
    right: 0;
    top: 0;
    width: 260px;
    height: 100%;
    background: var(--orange);
    clip-path: polygon(35% 0, 100% 0, 100% 100%, 0 100%, 0 38%);
  }

  .holder-name {
    position: absolute;
    left: 50px;
    top: 60px;
    font-family: "Exo 2", sans-serif;
    font-weight: 600;
    font-size: 27px;
    color: var(--orange);
  }
  .contact-list {
    position: absolute;
    left: 50px;
    top: 156px;
    list-style: none;
    font-family: "Open Sans", sans-serif;
    font-size: 15px;
    color: var(--grey);
  }
  .contact-list li {
    display: flex;
    align-items: center;
    height: 23px;
  }
  .contact-icon {
    width: 14px;
    height: 14px;
    margin-right: 6px;
    fill: var(--orange);
  }
  .brand {
    position: absolute;
    left: 50px;
    top: 252px;
    display: flex;
    align-items: center;
    gap: 12px;
  }
  .brand-dot {
    width: 48px;
    height: 48px;
    border-radius: 50%;
    background: var(--orange);
  }
  .brand-name {
    font-family: "Exo 2", sans-serif;
    font-weight: 600;
    font-size: 46px;
    line-height: 1;
    color: var(--ink);
  }

  .back-texture {
    position: absolute;
    inset: 0;
    background: radial-gradient(ellipse at center, var(--pattern-tone), var(--card-black));
  }
  .back-brand {
    position: absolute;
    left: 0;
    right: 0;
    top: 128px;
    text-align: center;
    font-family: "Exo 2", sans-serif;
    font-weight: 600;
    font-size: 78px;
    line-height: 1;
    color: var(--white);
  }
  .slogan {
    position: absolute;
    left: 0;
    right: 0;
    top: 214px;
    text-align: center;
    font-family: "Open Sans", sans-serif;
    font-weight: 600;
    font-size: 17px;
    letter-spacing: 3px;
    color: var(--white);
  }
</style>
</head>
<body>
  <section class="card card--front">
    <div class="accent-panel"></div>
    <h1 class="holder-name">Tobias Lindqvist</h1>
    <ul class="contact-list">
      <li>
        <svg class="contact-icon" viewBox="0 0 24 24" aria-hidden="true"><path d="M6.6 10.8a15.1 15.1 0 0 0 6.6 6.6l2.2-2.2a1 1 0 0 1 1-.25 11.4 11.4 0 0 0 3.6.57 1 1 0 0 1 1 1V20a1 1 0 0 1-1 1A17 17 0 0 1 3 4a1 1 0 0 1 1-1h3.5a1 1 0 0 1 1 1c0 1.25.2 2.45.57 3.57a1 1 0 0 1-.25 1z"/></svg>
        0031687203316
      </li>
      <li>
        <svg class="contact-icon" viewBox="0 0 24 24" aria-hidden="true"><path d="M2 5h20v14H2z M2 5l10 8 10-8" stroke="#fff" stroke-width="1.5"/></svg>
        Tobias@hartuvo.nl
      </li>
      <li>
        <svg class="contact-icon" viewBox="0 0 24 24" aria-hidden="true"><circle cx="12" cy="12" r="10"/></svg>
        www.hartuvo.nl
      </li>
    </ul>
    <div class="brand">
      <span class="brand-dot"></span>
      <span class="brand-name">hartuvo</span>
    </div>
  </section>

  <section class="card card--back">
    <div class="back-texture" role="img" aria-label="Faint repeating brand pattern in dark brown on black"></div>
    <p class="back-brand">hartuvo</p>
    <p class="slogan">Because Quality Matters</p>
  </section>
</body>
</html>
```